Business card design

I need my logo on this card, things I need the card to have on it
licensed and insured.
owner operators Milo & Trent Halvorsen
my phone number 5083716254
Disaster Recovery, Storm Damage Restoration, Proactive Disaster Plan Management, Roof Repair/Restoration Structural Repair and Reconstruction, Emergency Boarding and Tarping Service, Perimeter Fencing, Emergency Tree Removal,

```html
<!DOCTYPE html>
<html lang="en">
<head>
<meta charset="utf-8">
<title>Halvorsen's Construction L.L.C — Business Card</title>
<link href="https://fonts.googleapis.com/css2?family=Montserrat:wght@400;500;600&family=Overpass:wght@400&family=Quicksand:wght@500;600;700&display=swap" rel="stylesheet">
<style>
  :root {
    --backdrop: #d4d5d7;
    --card-dark: #161616;
    --card-light: #ffffff;
    --brand-blue: #3b8fd4;
    --ink-light: #f2f2f2;
    --ink-dark: #3c3c3c;
    --ink-grey: #5f6062;
    --rule-grey: #8a8b8d;
  }
  * { box-sizing: border-box; margin: 0; padding: 0; }
  html, body { width: 900px; height: 1200px; overflow: hidden; background: var(--backdrop); }
  .canvas { position: relative; width: 900px; height: 1200px; }

  .card { position: absolute; width: 633px; height: 364px; }
  .card--back { left: 133px; top: 210px; background: var(--card-dark); }
  .card--front { left: 134px; top: 624px; background: var(--card-light); }

  .brand {
    position: absolute; width: 260px;
    display: flex; flex-direction: column; align-items: center; gap: 16px;
  }
  .card--back .brand { left: 37px; top: 106px; }
  .card--front .brand { left: 27px; top: 104px; }
  .brand__mark { width: 84px; height: 84px; background: var(--brand-blue); }
  .brand__name {
    font-family: "Montserrat", sans-serif; font-weight: 400; font-size: 22px;
    line-height: 1.25; color: var(--brand-blue); text-align: center;
  }

  .services { position: absolute; left: 330px; top: 44px; }
  .services__title {
    font-family: "Montserrat", sans-serif; font-weight: 500; font-size: 17px;
    color: var(--brand-blue); letter-spacing: 0.3px; margin-bottom: 12px;
  }
  .services__list { list-style: none; font-family: "Overpass", sans-serif; font-size: 14px; color: var(--ink-light); letter-spacing: 0.3px; }
  .services__item { position: relative; padding-left: 20px; line-height: 22.5px; margin-bottom: 7.5px; }
  .services__item::before {
    content: ""; position: absolute; left: 1px; top: 5px; width: 10px; height: 10px;
    background: var(--brand-blue);
  }

  .divider { position: absolute; left: 307px; top: 95px; width: 1px; height: 176px; background: var(--rule-grey); }

  .contact { position: absolute; left: 326px; top: 92px; font-family: "Quicksand", sans-serif; color: var(--ink-dark); }
  .contact__names { font-size: 20px; font-weight: 700; color: var(--brand-blue); letter-spacing: 0.2px; }
  .contact__role { font-size: 15px; font-weight: 500; margin-top: 2px; letter-spacing: 0.6px; }
  .contact__address { font-size: 15px; font-weight: 500; line-height: 25px; margin-top: 9px; letter-spacing: 0.5px; }
  .contact__lines { list-style: none; margin-top: 7px; font-size: 15px; font-weight: 500; letter-spacing: 0.3px; }
  .contact__line { display: flex; align-items: center; gap: 6px; height: 23px; }
  .contact__line--phone { font-size: 16px; letter-spacing: 1.2px; }
  .contact__line svg { width: 15px; height: 15px; flex: none; }

  .credential { position: absolute; left: 0; right: 0; top: 307px; display: flex; align-items: center; gap: 8px; }
  .credential__rule { flex: 1; height: 1px; background: var(--brand-blue); }
  .credential__text {
    font-family: "Montserrat", sans-serif; font-weight: 600; font-size: 17px;
    color: var(--ink-grey); letter-spacing: 0.3px;
  }
</style>
</head>
<body>
<main class="canvas">

  <section class="card card--back" aria-label="Card back: services">
    <div class="brand">
      <span class="brand__mark"></span>
      <span class="brand__name">Halvorsen's Construction L.L.C</span>
    </div>
    <div class="services">
      <h2 class="services__title">OUR SERVICES:</h2>
      <ul class="services__list">
        <li class="services__item">Disaster Recovery</li>
        <li class="services__item">Storm Damage Restoration</li>
        <li class="services__item">Proactive Disaster Plan Management</li>
        <li class="services__item">Roof Repair/Restoration Structural<br>Repair and Reconstruction</li>
        <li class="services__item">Emergency Boarding and<br>Tarping Service</li>
        <li class="services__item">Perimeter Fencing</li>
        <li class="services__item">Emergency Tree Removal</li>
      </ul>
    </div>
  </section>

  <section class="card card--front" aria-label="Card front: contact">
    <div class="brand">
      <span class="brand__mark"></span>
      <span class="brand__name">Halvorsen's Construction L.L.C</span>
    </div>
    <div class="divider"></div>
    <div class="contact">
      <h1 class="contact__names">Milo &amp; Trent Halvorsen</h1>
      <p class="contact__role">Owner Operator</p>
      <p class="contact__address">214 Cedar Hollow Rd,<br>Greenville, SC 29601</p>
      <ul class="contact__lines">
        <li class="contact__line contact__line--phone">
          <svg viewBox="0 0 24 24" aria-hidden="true"><path fill="#3b8fd4" d="M6.6 10.8a15.1 15.1 0 0 0 6.6 6.6l2.2-2.2a1 1 0 0 1 1-.25 11.4 11.4 0 0 0 3.6.57 1 1 0 0 1 1 1V20a1 1 0 0 1-1 1A17 17 0 0 1 3 4a1 1 0 0 1 1-1h3.5a1 1 0 0 1 1 1c0 1.25.2 2.45.57 3.57a1 1 0 0 1-.25 1z"/></svg>
          5083716254
        </li>
        <li class="contact__line">
          <svg viewBox="0 0 24 24" aria-hidden="true"><rect x="2" y="5" width="20" height="14" fill="#3b8fd4"/><path d="M2 5l10 8 10-8" fill="none" stroke="#fff" stroke-width="1.8"/></svg>
          info@halvorsenconstructionllc.com
        </li>
        <li class="contact__line">
          <svg viewBox="0 0 24 24" aria-hidden="true"><g fill="none" stroke="#3b8fd4" stroke-width="1.8"><circle cx="12" cy="12" r="9.5"/><ellipse cx="12" cy="12" rx="4.2" ry="9.5"/><path d="M2.5 12h19M4 7h16M4 17h16"/></g></svg>
          halvorsenconstructionllc.com
        </li>
      </ul>
    </div>
    <div class="credential">
      <span class="credential__rule"></span>
      <span class="credential__text">LICENSED AND INSURED</span>
      <span class="credential__rule"></span>
    </div>
  </section>

</main>
</body>
</html>
```